Meal Plan Website Needs New Pages Designed

Brightwick Supper Kits is an online, membership based program that delivers weekly meal programs (7 days worth of recipes plus shopping lists) carefully crafted by an expert team of meal planners. All recipes are created to comply with the following macronutrient ratio: 65% healthy fats, 25% lean protein, 10% good carbs.
All recipes are Paleo friendly and a great resource for those individuals who want to correctly implement this type of diet.

We are re-designing our website and need the following pages designed:

· Home page w/ logo
· How it works page
· Get Started! page
· Recipes Page template (these will be the pages on our site that will have recipes)
· Kitchen Essentials Training page (this will be a page with videos and tips + tricks, PDFs, etc)

So 5 total PSDs, 1 for each page.

Target audience: Men and women between the ages of 30 and 60 who want to:
· Eat healthy
· Lose weight
· Follow/Implement the Paleo diet
· Take the guesswork out of preparing delicious AND healthy meals for them and their families
· Know exactly what to eat, what to buy, how to make it

Feelings/Messages we want to communicate through the design:
· “Organic” but elegant look
· Fresh/light/Airy
· Simple but NOT GENERIC
· “I want to get cooking” feeling

Our Stylistic preferences:
· Minimalist with a few bold elements (something in between)
· Easy to visually navigate (enough white space, but not too much)
· There is more to “see” than to “read”

Our Color Preferences:
· Lighter pallet
· Colors that evoke natural woods, granite countertops…
· Stay away from using all dark colors

Our Font Type Preferences:
· Easy to read
· Not more than 3 font types
· Not too rigid
· Not too sophisticated
· Simple with a touch

Examples of Website Designs that we like:
· http://www.dorvanta.com/meal-plans/
· http://grulvix.com/
· https://www.mistobarn.com/

```html
<!DOCTYPE html>
<html lang="en">
<head>
<meta charset="utf-8">
<title>Brightwick Supper Kits</title>
<link href="https://fonts.googleapis.com/css2?family=Sorts+Mill+Goudy&family=Source+Sans+3:ital,wght@0,400;0,600;1,400&display=swap" rel="stylesheet">
<style>
:root{
  --gold:#b08a55;
  --gold-dark:#9c7645;
  --sand:#dcc49c;
  --rule:#c9ae82;
  --ink:#333;
  --muted:#858585;
  --card:#f7f6f4;
  --band:#f4f4f4;
  --header:rgba(38,38,38,.74);
  --social:#3b3b3b;
}
*{margin:0;padding:0;box-sizing:border-box}
html,body{width:763px;height:1200px;overflow:hidden;background:#fff}
body{position:relative;font-family:"Source Sans 3",Arial,sans-serif;color:var(--ink)}
.abs{position:absolute}
.serif{font-family:"Sorts Mill Goudy",Georgia,serif;font-weight:400}

/* hero */
.hero-panel{position:absolute;top:0;height:344px}
.hero-salad{left:0;width:249px;background:
  radial-gradient(ellipse 45% 30% at 62% 38%,rgba(110,150,60,.75),rgba(110,150,60,0) 70%),
  radial-gradient(ellipse 70% 38% at 48% 55%,rgba(205,140,85,.95),rgba(220,170,120,.6) 55%,rgba(236,233,229,0) 80%),
  linear-gradient(170deg,#f3f2f0 0%,#e5e3df 55%,#f4f4f3 100%)}
.hero-cake{left:258px;width:248px;background:
  radial-gradient(ellipse 60% 50% at 45% 45%,rgba(214,196,170,.75),rgba(214,196,170,0) 70%),
  radial-gradient(ellipse 80% 70% at 55% 40%,#a87c52 0%,#8e6640 55%,rgba(142,102,64,0) 85%),
  linear-gradient(160deg,#b9a48a 0%,#7a6a58 60%,#6f8c8a 100%)}
.hero-pizza{left:514px;width:249px;background:
  radial-gradient(ellipse 30% 22% at 40% 30%,rgba(120,190,60,.7),rgba(120,190,60,0) 70%),
  radial-gradient(ellipse 30% 22% at 72% 62%,rgba(120,190,60,.6),rgba(120,190,60,0) 70%),
  radial-gradient(ellipse 90% 80% at 65% 55%,#d2502f 0%,#c9502f 55%,#c98a4c 78%,#6e5a48 100%)}
.hero-arrow{position:absolute;top:178px;width:33px;height:33px;border-radius:50%;background:rgba(55,55,55,.6)}
.hero-arrow svg{position:absolute;left:10px;top:9px}

/* header */
.site-header{position:absolute;left:0;top:0;width:763px;height:54px;background:var(--header)}
.brand{position:absolute;left:84px;top:15px;display:flex;align-items:center;gap:10px}
.brand-dot{width:22px;height:22px;border-radius:50%;border:3px solid #fff}
.brand-name{font-size:22px;color:#f1e2c6;line-height:1}
.nav{position:absolute;top:30px;left:416px;display:flex;gap:19px;font-size:8.6px;font-weight:600;color:#fff;text-transform:uppercase;letter-spacing:-.2px}

/* features */
.feature{position:absolute;top:392px;width:191px;height:208px;background:var(--card);text-align:center}
.feature-icon{position:absolute;left:65px;top:17px;width:61px;height:61px;border-radius:50%;border:3px solid var(--gold);background:#efe3cf}
.feature-icon svg{position:absolute;left:14px;top:14px}
.feature-title{position:absolute;left:0;top:91px;width:100%;font-size:17px;color:#333}
.feature-text{position:absolute;left:8px;top:119px;width:175px;font-size:8.5px;line-height:12.3px;color:var(--muted)}
.btn{position:absolute;height:23px;border:1px solid var(--gold-dark);background:linear-gradient(#e8d5b2,#d6bb8c);color:var(--gold-dark);font-size:8.5px;line-height:21px;text-align:center}
.feature .btn{left:57px;top:169px;width:79px}

/* about */
.about-art{left:84px;top:642px;width:136px;height:178px;background:
  radial-gradient(ellipse 38% 22% at 62% 22%,rgba(226,40,40,.55),rgba(226,40,40,0) 75%),
  radial-gradient(ellipse 28% 36% at 60% 68%,rgba(245,206,40,.75),rgba(245,206,40,0) 75%),
  radial-gradient(ellipse 60% 40% at 62% 28%,#f6f6f6,#fff 80%)}
.about-title{left:239px;top:656px;font-size:18.5px;color:#333}
.about-title span{color:var(--gold)}
.about-text{left:241px;top:692px;width:434px;font-size:8.6px;line-height:15.4px;color:#6f6f6f}
.about .btn{left:243px;top:788px;width:82px}

/* team */
.team{left:0;top:859px;width:763px;height:174px;background:var(--band)}
.team-title{left:0;top:21px;width:763px;text-align:center;font-size:15.5px;color:#444}
.team-arrow{position:absolute;top:26px;width:12px;height:12px;background:#9a9a9a}
.team-arrow svg{position:absolute;left:3px;top:2px}
.avatar{position:absolute;top:70px;width:64px;height:64px;border-radius:50%;border:3px solid #fff;box-shadow:0 0 0 1px #dcdcdc}
.avatar-a{background:radial-gradient(circle at 50% 40%,#f0d3bf 0%,#d9b59a 35%,#e7ebee 75%)}
.avatar-b{background:radial-gradient(circle at 50% 42%,#e3c2a6 0%,#c9a58a 35%,#a8c4da 80%)}
.quote{position:absolute;top:81px;width:208px;font-size:8.4px;line-height:12.8px;color:#868686}
.quote-mark{position:absolute;top:74px;font-size:17px;line-height:1;color:#bbb;font-family:Georgia,serif}
.quote-by{position:absolute;top:132px;font-size:8.6px;font-style:italic;color:var(--gold);text-align:right}

/* footer */
.footer{left:0;top:1033px;width:763px;height:167px;background:var(--sand)}
.footer-head{position:absolute;top:17px;font-size:13px;color:#3a3a3a}
.field{position:absolute;left:84px;width:167px;height:21px;background:#fff;font-size:8.3px;font-style:italic;color:#777;padding:4px 9px}
.submit{position:absolute;left:84px;top:95px;width:59px;height:21px;background:var(--gold);color:#fff;font-size:9px;font-weight:600;text-align:center;line-height:21px;letter-spacing:.3px}
.divider{position:absolute;top:15px;width:1px;height:108px;background:var(--rule)}
.social{position:absolute;top:47px;width:28px;height:28px;border-radius:50%;background:var(--social)}
.social svg{position:absolute;left:7px;top:7px}
.support{position:absolute;left:514px;top:44px;width:168px;height:26px}
.support span{position:absolute;left:28px;top:5px;color:#fff;font-size:11.5px;font-weight:600}
.footer-rule{position:absolute;left:84px;top:134px;width:597px;height:1px;background:var(--rule)}
.footer-links{position:absolute;left:84px;top:147px;font-size:8px;color:var(--gold-dark)}
.footer-links i{font-style:normal;margin:0 6px}
.copyright{position:absolute;right:83px;top:146px;font-size:7.6px;color:var(--gold-dark)}
</style>
</head>
<body>

<section class="hero" aria-label="Featured dishes">
  <div class="hero-panel hero-salad" role="img" aria-label="Photo of a grilled chicken salad on a white plate"></div>
  <div class="hero-panel hero-cake" role="img" aria-label="Photo of an iced nut loaf on baking paper"></div>
  <div class="hero-panel hero-pizza" role="img" aria-label="Photo of a pizza with peppers, onion and olives"></div>
  <div class="hero-arrow" style="left:5px"><svg width="14" height="16" viewBox="0 0 14 16"><path d="M10 1 3 8l7 7" fill="none" stroke="#fff" stroke-width="1.6"/></svg></div>
  <div class="hero-arrow" style="left:725px"><svg width="14" height="16" viewBox="0 0 14 16"><path d="M4 1l7 7-7 7" fill="none" stroke="#fff" stroke-width="1.6"/></svg></div>
</section>

<header class="site-header">
  <div class="brand">
    <div class="brand-dot"></div>
    <div class="brand-name serif">Brightwick Supper Kits</div>
  </div>
  <nav class="nav"><span>Meal Plans</span><span>About</span><span>How it works</span><span>Resources</span><span>Blog</span></nav>
</header>

<section class="features">
  <article class="feature" style="left:82px">
    <div class="feature-icon"><svg width="27" height="27" viewBox="0 0 26 26"><path d="M3 13h20a10 9 0 0 1-20 0z" fill="#a77a3f"/><path d="M12 3c-2 2 2 3 0 6M15 3c-2 2 2 3 0 6" fill="none" stroke="#a77a3f" stroke-width="1.3"/></svg></div>
    <h3 class="feature-title serif">Meal Plans</h3>
    <p class="feature-text">Lorem ipsum dolor sit amet, consectetur adipisic ing elit, sed do eiusmod tempor incididunt ut labore et dolore magna aliqua.</p>
    <div class="btn">Learn More &gt;&gt;</div>
  </article>
  <article class="feature" style="left:286px">
    <div class="feature-icon"><svg width="27" height="27" viewBox="0 0 26 26"><rect x="3" y="5" width="17" height="17" rx="3" fill="none" stroke="#a77a3f" stroke-width="2.4"/><path d="M11 16l1-4 9-9 3 3-9 9z" fill="#a77a3f"/></svg></div>
    <h3 class="feature-title serif">QuickStart Guide</h3>
    <p class="feature-text">Lorem ipsum dolor sit amet, consectetur adipisic ing elit, sed do eiusmod tempor incididunt ut labore et dolore magna aliqua.</p>
    <div class="btn">Learn More &gt;&gt;</div>
  </article>
  <article class="feature" style="left:490px">
    <div class="feature-icon"><svg width="27" height="27" viewBox="0 0 26 26"><rect x="1" y="9" width="3" height="8" fill="#a77a3f"/><rect x="5" y="6" width="4" height="14" fill="#a77a3f"/><rect x="9" y="12" width="8" height="2.5" fill="#a77a3f"/><rect x="17" y="6" width="4" height="14" fill="#a77a3f"/><rect x="22" y="9" width="3" height="8" fill="#a77a3f"/></svg></div>
    <h3 class="feature-title serif">At Home Workouts</h3>
    <p class="feature-text">Lorem ipsum dolor sit amet, consectetur adipisic ing elit, sed do eiusmod tempor incididunt ut labore et dolore magna aliqua.</p>
    <div class="btn">Learn More &gt;&gt;</div>
  </article>
</section>

<section class="about">
  <div class="abs about-art" role="img" aria-label="Cartoon character thinking under a red question mark bubble"></div>
  <h2 class="abs about-title serif">What is a <span>Brightwick Supper Kits?</span></h2>
  <p class="abs about-text">Sed ut perspiciatis unde omnis iste natus error sit voluptatem accusantium doloremque laudantium, totam rem aper, eaque ipsa quae ab illo inventore veritatis et quasi architecto beatae vitae dicta sunt explicabo. Nemo enimvolu quia voluptas sit aspernatur aut odit aut fugit, sed quia consequuntur magni dolores. Sed ut perspiciatis unde omnis iste natus error sit voluptatem accusantium doloremque laudantium, totam rem aeriam, eaque ipsa quae ab illo inventore veritatis et quasi architecto beatae vitae dicta sunt explicabo.</p>
  <div class="btn">Learn More &gt;&gt;</div>
</section>

<section class="abs team">
  <h2 class="abs team-title serif">An Expert team dedicated to your success</h2>
  <div class="team-arrow" style="left:656px"><svg width="6" height="8" viewBox="0 0 6 8"><path d="M5 0 1 4l4 4" fill="none" stroke="#fff"/></svg></div>
  <div class="team-arrow" style="left:669px"><svg width="6" height="8" viewBox="0 0 6 8"><path d="M1 0l4 4-4 4" fill="none" stroke="#fff"/></svg></div>

  <div class="avatar avatar-a" style="left:84px" role="img" aria-label="Portrait photo of a smiling team member"></div>
  <span class="quote-mark" style="left:161px">&ldquo;</span>
  <p class="quote" style="left:162px">&nbsp;&nbsp;&nbsp;&nbsp;Neque porro quisquam est, qui dolorem ipsum quia dolor sit amet, consectetur, adipisci velit, sed quia non numquamu eius modi tempora incidunt ut labore et dolore magnam velt aliquam quaerat voluptatem.</p>
  <p class="quote-by" style="left:268px;width:100px">by Nora Pell</p>

  <div class="avatar avatar-b" style="left:394px" role="img" aria-label="Portrait photo of a smiling team member"></div>
  <span class="quote-mark" style="left:471px">&ldquo;</span>
  <p class="quote" style="left:472px">&nbsp;&nbsp;&nbsp;&nbsp;Neque porro quisquam est, qui dolorem ipsum quia dolor sit amet, consectetur, adipisci velit, sed quia non numquamu eius modi tempora incidunt ut labore et dolore magnam velt aliquam quaerat voluptatem.</p>
  <p class="quote-by" style="left:578px;width:100px">by Nora Pell</p>
</section>

<footer class="abs footer">
  <h4 class="footer-head serif" style="left:84px">Get a Free Meal Plan!</h4>
  <div class="field" style="top:41px">Enter your Name...</div>
  <div class="field" style="top:67px">Enter your Email...</div>
  <div class="submit">SUBMIT</div>

  <div class="divider" style="left:295px"></div>
  <h4 class="footer-head serif" style="left:314px">Follow Us!</h4>
  <div class="social" style="left:312px" role="img" aria-label="Social link"><svg width="14" height="14" viewBox="0 0 14 14"><path d="M6 8l2-2M5 5.5 3.5 7a2 2 0 0 0 3 3L8 8.5M9 8.5 10.5 7a2 2 0 0 0-3-3L6 5.5" fill="none" stroke="#fff" stroke-width="1.4" stroke-linecap="round"/></svg></div>
  <div class="social" style="left:347px" role="img" aria-label="Social link"><svg width="14" height="14" viewBox="0 0 14 14"><path d="M6 8l2-2M5 5.5 3.5 7a2 2 0 0 0 3 3L8 8.5M9 8.5 10.5 7a2 2 0 0 0-3-3L6 5.5" fill="none" stroke="#fff" stroke-width="1.4" stroke-linecap="round"/></svg></div>
  <div class="social" style="left:383px" role="img" aria-label="Social link"><svg width="14" height="14" viewBox="0 0 14 14"><path d="M6 8l2-2M5 5.5 3.5 7a2 2 0 0 0 3 3L8 8.5M9 8.5 10.5 7a2 2 0 0 0-3-3L6 5.5" fill="none" stroke="#fff" stroke-width="1.4" stroke-linecap="round"/></svg></div>
  <div class="social" style="left:418px" role="img" aria-label="Social link"><svg width="14" height="14" viewBox="0 0 14 14"><path d="M6 8l2-2M5 5.5 3.5 7a2 2 0 0 0 3 3L8 8.5M9 8.5 10.5 7a2 2 0 0 0-3-3L6 5.5" fill="none" stroke="#fff" stroke-width="1.4" stroke-linecap="round"/></svg></div>
  <div class="social" style="left:454px" role="img" aria-label="Social link"><svg width="14" height="14" viewBox="0 0 14 14"><path d="M6 8l2-2M5 5.5 3.5 7a2 2 0 0 0 3 3L8 8.5M9 8.5 10.5 7a2 2 0 0 0-3-3L6 5.5" fill="none" stroke="#fff" stroke-width="1.4" stroke-linecap="round"/></svg></div>

  <div class="divider" style="left:514px"></div>
  <h4 class="footer-head serif" style="left:531px">Customer Services</h4>
  <div class="support">
    <svg width="168" height="26" viewBox="0 0 168 26"><path d="M0 0h160l-8 13 8 13H0z" fill="#b08a55"/><path d="M124 10l4 3-4 3z" fill="#fff"/></svg>
    <span>Click For Support</span>
  </div>

  <div class="footer-rule"></div>
  <p class="footer-links">PRESS<i>|</i>TERMS<i>|</i>CONTACT</p>
  <p class="copyright">Copyright 2014 &copy; Brightwick Supper Kits. All rights reserved</p>
</footer>

</body>
</html>
```